Business Card Design Competition

We need a business card design for our Internet Marketing company. We require both front and back designs and the final card must be 89x53mm in size, plus crop marks to 91x55mm. Colours as per logo, plus perhaps black and/or grey (#828282).
Final text must be editable (if you can supply an editable Fireworks PNG, even better)...
FRONT TEXT:
Full Name
Position
Address Line
Suburb, State, Postcode
Phone: 0000 000 000
Mobile: 0000 000 000
Email: xxx@brightlanemedia.com.au
Web: www.brightlanemedia.com.au
Rear of card should be a fresh design plus our slogan text: "Getting You Noticed" in large font, then in small text "Kestrel Holdings Pty Ltd (ABN: 42 561 903 774)".
Target Market(s)
Small/Medium Businesses
Industry/Entity Type
Business

```html
<!DOCTYPE html>
<html lang="en">
<head>
<meta charset="utf-8">
<title>Brightlane Media – Business Card Front</title>
<link rel="stylesheet" href="https://fonts.googleapis.com/css2?family=Tinos&display=swap">
<style>
  :root {
    --paper-light: #f1f1f1;
    --paper-mid: #e4e4e4;
    --ink: #2b2b2b;
    --tab-black: #050505;
    --tab-rim: #b9b9b9;
    --tab-rim-light: #e2e2e2;
    --brand-green: #8dc63f;
    --brand-orange: #f7931e;
  }
  html, body {
    margin: 0;
    padding: 0;
    overflow: hidden;
  }
  .card {
    position: relative;
    width: 1200px;
    height: 726px;
    overflow: hidden;
    background: radial-gradient(ellipse at 45% 40%, var(--paper-light) 0%, var(--paper-mid) 100%);
    font-family: "Tinos", "Times New Roman", serif;
    color: var(--ink);
  }
  .brand-tab {
    position: absolute;
    left: 0;
    top: 536px;
    width: 296px;
    height: 94px;
  }
  .brand-mark {
    position: absolute;
    left: 84px;
    top: 556px;
    width: 56px;
    height: 56px;
    border-radius: 50%;
    background: var(--brand-orange);
  }
  .brand-name {
    position: absolute;
    left: 150px;
    top: 560px;
    margin: 0;
    font-size: 21px;
    line-height: 24px;
    font-weight: 400;
    color: var(--brand-green);
  }
  .contact {
    position: absolute;
    right: 128px;
    top: 233px;
    margin: 0;
    text-align: right;
    font-size: 33px;
    line-height: 43.5px;
    font-style: normal;
  }
  .contact p {
    margin: 0;
  }
  .contact .address-block {
    margin-top: 43.5px;
  }
</style>
</head>
<body>
  <main class="card">
    <svg class="brand-tab" viewBox="0 0 296 94" aria-hidden="true">
      <defs>
        <linearGradient id="rim" x1="0" y1="0" x2="0" y2="1">
          <stop offset="0" stop-color="var(--tab-rim-light)"/>
          <stop offset="1" stop-color="var(--tab-rim)"/>
        </linearGradient>
      </defs>
      <path d="M0 0 H250 A46 46 0 0 1 250 94 H0 Z" fill="url(#rim)"/>
      <path d="M0 8 H246 A39 39 0 0 1 246 86 H0 Z" fill="var(--tab-black)"/>
    </svg>
    <span class="brand-mark" aria-hidden="true"></span>
    <p class="brand-name">Brightlane<br>Media</p>

    <address class="contact">
      <p class="name">Full Name</p>
      <p class="position">Position</p>
      <div class="address-block">
        <p>Address Line</p>
        <p>Suburb, State, Postcode</p>
        <p>Phone: 0000 000 000</p>
        <p>Mobile: 0000 000 000</p>
        <p>Email: xxx@brightlanemedia.com.au</p>
        <p>Web: www.brightlanemedia.com.au</p>
      </div>
    </address>
  </main>
</body>
</html>
```